Fitness website

Website for a fitness brand (see attached specs). Design needs to be modern and vibrant with CTAs on every page. We will provide logos, images, etc but for now user placeholder text and images. For now use the name 'Corvane Athletics' as the name to use on the design. The goal of this site is to either get people to join the gym (5 physical locations across the US); buy an online program; buy merch or supplements or sign up for the newsletter. Pleas use images from this foldeR: https://filebarn.example/share/folders/8QwTz41mKpLrXv93NdYe7HsaBuJ0Cf2_R?usp=sharing

We will be coding this in ReactNative. Lots more work for the winner as well, this is a 1st project for us.

Target Market(s)

fitness enthusiats

Industry/Entity Type

fitness, health, wellness

Number of Pages Required

5+ page

Font styles to use
Other font styles liked:
• Lato

Colors
0054AA
0677BA
7BADD7
CADEEF
E8F1F8
0094D4
00A9DD
6FCCEA
C7EBF8
E9F6FB
00AB8E
00BBA5
67D7C9
C6EFE9
E9F9F6
EE7325
F08F49
F5BC92
FAE3D3
FDF4ED

Requirements
Must have
• must be reactive. most people will view it first on mobile
Nice to have
• video in hero section of top of home page

```html
<!DOCTYPE html>
<html lang="en">
<head>
<meta charset="utf-8">
<title>Corvane Athletics</title>
<link href="https://fonts.googleapis.com/css2?family=Exo+2:ital,wght@1,700;1,800&family=Lato:ital,wght@0,400;0,700;0,900;1,400&display=swap" rel="stylesheet">
<style>
:root{
  --blue-deep:#0054AA;
  --blue-mid:#0677BA;
  --blue-bright:#0094D4;
  --orange:#EE7325;
  --ink:#15181d;
  --hero-bg:#1b1f26;
  --text:#2b2f36;
  --muted:#6b717a;
  --line:#d5d9df;
  --white:#ffffff;
}
*{margin:0;padding:0;box-sizing:border-box}
html,body{width:1200px;height:3954px;overflow:hidden}
body{position:relative;font-family:"Lato",sans-serif;color:var(--text);background:var(--white)}
.abs{position:absolute}
.display{font-family:"Exo 2",sans-serif;font-style:italic;font-weight:800}
.btn{position:absolute;display:flex;align-items:center;justify-content:center;gap:12px;font-size:14px;color:var(--white);border-radius:3px;font-weight:400}
.btn-blue{background:var(--blue-bright)}
.btn-orange{background:var(--orange)}
.ph{position:absolute}

/* top bar */
.topbar{top:0;left:0;width:1200px;height:49px;border-bottom:1px solid var(--line)}
.topbar .mail{left:140px;top:15px;font-size:12px;display:flex;gap:8px;align-items:center}
.topbar .aff{left:675px;top:16px;font-size:12px}
.topbar .loc{left:970px;top:16px;font-size:12px}
.chev{position:absolute;top:18px}
.account{left:790px;top:6px;width:160px;height:37px;background:var(--blue-deep);border-radius:3px;color:#fff;font-size:12px;display:flex;align-items:center;justify-content:center;gap:8px}

/* nav */
.logo{left:140px;top:58px;font-weight:900;font-size:22px;color:var(--ink);line-height:1.05;letter-spacing:.5px}
.nav{left:0;top:74px;font-size:14px;color:var(--ink)}
.nav span{position:absolute;white-space:nowrap}
.nav .active{color:var(--blue-deep);font-weight:700}
.search{left:772px;top:63px;width:290px;height:37px;border:1px solid #b9c0c8;border-radius:3px;font-size:11px;color:var(--muted);padding:11px 18px}
.search .go{position:absolute;right:-1px;top:-1px;width:64px;height:37px;background:var(--blue-bright);border-radius:0 3px 3px 0;display:flex;align-items:center;justify-content:center}

/* hero */
.hero{top:121px;left:0;width:1200px;height:590px;background:var(--hero-bg);overflow:hidden}
.hero-photo{left:560px;top:0;width:640px;height:590px;background:linear-gradient(100deg,#1b1f26 0%,#3a3f47 25%,#6b6f74 60%,#2d3138 100%)}
.hero h1{left:138px;top:150px;font-size:58px;line-height:69px;color:var(--blue-bright)}
.hero h1 em{color:var(--orange);font-style:inherit}
.hero p{left:139px;top:293px;font-size:17px;color:#fff}
.dashes{left:139px;top:494px;display:flex;gap:16px}
.dashes i{display:block;width:17px;height:2px;background:#fff}
.dashes i.on{background:var(--blue-bright)}

/* about */
.about-title{left:152px;top:770px;font-size:56px;color:var(--blue-bright)}
.about-copy{left:152px;top:845px;width:412px;font-size:14.5px;line-height:24px;color:var(--text)}
.about-photo{left:611px;top:729px;width:589px;height:477px;background:linear-gradient(135deg,#1f2a3a,#4d6a8a 45%,#8aa4bd 60%,#263243)}

/* programs */
.programs-title{left:0;width:1200px;top:1296px;text-align:center;font-size:58px;color:#fff}
.card{position:absolute;top:1390px;width:293px;height:389px;background:#fff}
.card .img{position:absolute;left:8px;top:9px;width:277px;height:200px}
.card h3{position:absolute;left:28px;top:228px;font-size:18px;font-weight:700;color:var(--ink)}
.card p{position:absolute;left:28px;top:256px;width:230px;font-size:11px;line-height:15px;color:var(--muted)}
.card .btn{top:335px;left:26px;width:97px;height:29px;font-size:11px;font-weight:700}
.pdots{left:555px;top:1823px;display:flex;gap:10px}
.pdots i{width:10px;height:10px;border-radius:50%;background:var(--orange);display:block}

/* testimonials */
.testi-title{left:0;width:1200px;top:1955px;text-align:center;font-size:58px;color:var(--blue-bright)}
.avatar{position:absolute;top:2052px;width:86px;height:86px;border-radius:50%;border:3px solid var(--blue-bright)}
.quote{left:220px;top:2156px;width:760px;text-align:center;font-style:italic;font-size:20px;line-height:25px;color:var(--text)}
.stars{left:0;width:1200px;top:2250px;display:flex;justify-content:center;gap:10px}
.author{left:0;width:1200px;top:2296px;text-align:center;font-size:20px;color:var(--text)}

/* cta band */
.cta{top:2398px;left:0;width:1200px;height:518px;background:radial-gradient(ellipse at 40% 50%,#1d62b0 0%,var(--blue-deep) 55%,#0a4a96 100%)}
.cta h2{left:0;width:1200px;top:117px;text-align:center;font-size:58px;color:#fff}
.cta p{left:210px;width:780px;top:198px;text-align:center;font-size:20px;line-height:25px;color:#fff}

/* blog */
.blog-title{left:0;width:1190px;top:2970px;text-align:center;font-size:40px;color:var(--ink)}
.post{position:absolute;top:3053px;width:293px}
.post .img{height:208px;border-radius:3px}
.post h4{margin:13px 0 0 6px;font-size:15.5px;line-height:19px;font-weight:700;color:var(--ink);text-transform:uppercase}
.post .meta{margin:16px 0 0 6px;font-size:11px;color:var(--muted);display:flex;gap:8px;align-items:center}

/* newsletter */
.news{top:3474px;left:0;width:1200px;height:134px;background:var(--blue-mid)}
.news h2{left:153px;top:44px;font-size:40px;font-weight:900;color:#fff;letter-spacing:.5px}
.news .field{left:463px;top:46px;width:524px;height:46px;background:#fff;border:1px solid #222;border-radius:4px;font-size:14px;font-weight:700;color:var(--ink);padding:14px 15px}
.news .send{position:absolute;right:-1px;top:-1px;width:58px;height:46px;background:var(--ink);border-radius:0 4px 4px 0;display:flex;align-items:center;justify-content:center}

/* footer */
.footer{top:3608px;left:0;width:1200px;height:346px;background:#0c0d0f;color:#fff}
.fcol{position:absolute;top:73px}
.fcol h5{font-size:20px;font-weight:700;color:var(--blue-mid);text-transform:uppercase;margin-bottom:16px;white-space:nowrap}
.fcol li{list-style:none;font-size:12px;line-height:24px;display:flex;align-items:center;gap:12px}
.frule{left:139px;top:274px;width:923px;height:1px;background:#333}
.legal{left:139px;top:296px;font-size:12px;display:flex;gap:13px}
.pay{left:704px;top:290px;width:204px;height:29px;background:#fff;border-radius:3px;display:flex;align-items:center;justify-content:space-around;padding:0 8px}
.pay i{display:block;width:28px;height:14px;border-radius:2px;background:#c9ced6}
.social{left:920px;top:299px;display:flex;gap:17px}
.social i{display:block;width:12px;height:12px;border-radius:50%;background:#fff}
</style>
</head>
<body>

<!-- top bar -->
<div class="abs topbar">
  <div class="abs mail">
    <svg width="14" height="11" viewBox="0 0 14 11"><rect x="0.7" y="0.7" width="12.6" height="9.6" rx="1" fill="none" stroke="#222" stroke-width="1.3"/><path d="M1 1.5 7 6l6-4.5" fill="none" stroke="#222" stroke-width="1.3"/></svg>
    info@corvaneathletics.example
  </div>
  <div class="abs aff">Affiliates</div>
  <svg class="chev" style="left:755px" width="10" height="7" viewBox="0 0 10 7"><path d="M1 1l4 4 4-4" fill="none" stroke="#0677BA" stroke-width="1.5"/></svg>
  <div class="abs account">
    <svg width="13" height="14" viewBox="0 0 13 14"><circle cx="6.5" cy="4" r="3" fill="none" stroke="#fff" stroke-width="1.3"/><path d="M1 13c0-3 2.5-5 5.5-5s5.5 2 5.5 5" fill="none" stroke="#fff" stroke-width="1.3"/></svg>
    My Account
  </div>
  <div class="abs loc">Locations</div>
  <svg class="chev" style="left:1048px" width="10" height="7" viewBox="0 0 10 7"><path d="M1 1l4 4 4-4" fill="none" stroke="#0677BA" stroke-width="1.5"/></svg>
</div>

<!-- nav -->
<div class="abs logo">CORVANE<br>ATHLETICS</div>
<div class="abs nav">
  <svg class="abs" style="left:362px;top:-11px" width="6" height="6"><circle cx="3" cy="3" r="3" fill="#0677BA"/></svg>
  <span class="active" style="left:344px">Home</span>
  <span style="left:400px">About Us</span>
  <span style="left:476px">Programs</span>
  <span style="left:552px">Shop</span>
  <span style="left:598px">Blog</span>
  <span style="left:643px">Contact</span>
</div>
<div class="abs search">Search
  <div class="go"><svg width="17" height="17" viewBox="0 0 17 17"><circle cx="7" cy="7" r="5.5" fill="none" stroke="#fff" stroke-width="2"/><path d="M11 11l4.5 4.5" stroke="#fff" stroke-width="2.2" stroke-linecap="round"/></svg></div>
</div>

<!-- hero -->
<section class="abs hero">
  <div class="ph hero-photo" role="img" aria-label="Athlete performing a bar muscle-up in a gym rig"></div>
  <svg class="abs" style="left:0;top:0" width="1200" height="590" viewBox="0 0 1200 590">
    <polygon points="0,528 580,551 1200,586 1200,590 0,590" fill="#fff"/>
    <polygon points="0,528 580,551 0,585" fill="#0094D4"/>
  </svg>
  <h1 class="abs display">Fitness. <em>Lifestyle.</em><br>Balance.</h1>
  <p class="abs">Functional training for everyday strength and mobility.</p>
  <div class="btn btn-blue" style="left:138px;top:355px;width:141px;height:44px">Join the Gym
    <svg width="12" height="12" viewBox="0 0 12 12"><path d="M1 1l10 10M11 4v7H4" fill="none" stroke="#fff" stroke-width="1.5"/></svg></div>
  <div class="btn btn-orange" style="left:298px;top:355px;width:190px;height:44px">Buy an Online Program</div>
  <div class="abs dashes"><i></i><i class="on"></i><i></i><i></i></div>
</section>

<!-- about -->
<h2 class="abs display about-title">About Us</h2>
<p class="abs about-copy">Lorem ipsum dolor sit amet, consectetur adipiscing elit, sed do eiusmod tempor incididunt ut labore et dolore magna aliqua. Quis ipsum suspendisse ultrices gravida. Risus commodo viverra maecenas accumsan lacus vel facilisis. Lorem ipsum dolor sit amet, consectetur adipiscing elit, sed do eiusmod tempor incididunt ut labore et dolore magna aliqua. Quis ipsum suspendisse ultrices gravida. Risus commodo viverra maecenas accumsan lacus vel facilisis. Lorem ipsum dolor sit amet, consectetur adipiscing elit, sed do eiusmod tempor incididunt ut labore et dolore magna aliqua. Quis ipsum suspendisse ultrices gravida. Risus</p>
<div class="btn btn-blue" style="left:152px;top:1133px;width:143px;height:45px">Join the Gym
  <svg width="12" height="12" viewBox="0 0 12 12"><path d="M1 1l10 10M11 4v7H4" fill="none" stroke="#fff" stroke-width="1.5"/></svg></div>
<div class="ph about-photo" role="img" aria-label="Athlete lifting a loaded barbell during a workout"></div>

<!-- programs -->
<svg class="abs" style="left:0;top:1210px" width="1200" height="712" viewBox="0 0 1200 712">
  <polygon points="0,4 600,46 1200,2 1200,710 600,678 0,710" fill="#0054AA"/>
</svg>
<h2 class="abs display programs-title">Programs</h2>
<div class="card" style="left:138px">
  <div class="img" role="img" aria-label="Athletes lifting barbells overhead" style="background:linear-gradient(160deg,#2a3442,#5f7388 50%,#1d2531)"></div>
  <h3>Masters</h3>
  <p>Lorem ipsum dolor sit amet, consectetur adipiscing elit, sed do eiusmod tempor incididunt ut labore et dolore magna aliquac</p>
  <div class="btn btn-orange">BOOK NOW</div>
</div>
<div class="card" style="left:453px">
  <div class="img" role="img" aria-label="Athlete training with battle ropes" style="background:linear-gradient(160deg,#8e9399,#c9ced2 50%,#6f757c)"></div>
  <h3>Functional Fitness</h3>
  <p>Lorem ipsum dolor sit amet, consectetur adipiscing elit, sed do eiusmod tempor incididunt ut labore et dolore magna aliquac</p>
  <div class="btn btn-blue">BOOK NOW</div>
</div>
<div class="card" style="left:767px">
  <div class="img" role="img" aria-label="Competitor pushing through a workout" style="background:linear-gradient(160deg,#3b3f44,#7c7a73 50%,#2a2d31)"></div>
  <h3>Competitive</h3>
  <p>Lorem ipsum dolor sit amet, consectetur adipiscing elit, sed do eiusmod tempor incididunt ut labore et dolore magna aliquac</p>
  <div class="btn btn-blue">BOOK NOW</div>
</div>
<div class="abs pdots"><i></i><i></i><i></i><i></i><i></i></div>

<!-- testimonials -->
<h2 class="abs display testi-title">Testimonials</h2>
<div class="avatar" role="img" aria-label="Member portrait" style="left:331px;background:#8b8f94"></div>
<div class="avatar" role="img" aria-label="Member portrait" style="left:443px;background:#a9b8c8"></div>
<div class="avatar" role="img" aria-label="Member portrait" style="left:555px;background:#4a3f3a"></div>
<div class="avatar" role="img" aria-label="Member portrait" style="left:668px;background:#e5b54a"></div>
<div class="avatar" role="img" aria-label="Member portrait" style="left:781px;background:#b8c6d2"></div>
<p class="abs quote">Lorem ipsum dolor sit amet, consectetur adipiscing elit, sed do eiusmod tempor incididunt ut labore et dolore magna aliqua. Quis ipsum suspendisse ultrices gravida. Risus commodo viverra maecenas accumsan lacus vel facilisis.</p>
<div class="abs stars">
  <svg width="24" height="24" viewBox="0 0 24 24"><path d="M12 1l3.3 7 7.7.9-5.7 5.2 1.6 7.6L12 17.8 5.1 21.7l1.6-7.6L1 8.9 8.7 8z" fill="#1b1b1b"/></svg>
  <svg width="24" height="24" viewBox="0 0 24 24"><path d="M12 1l3.3 7 7.7.9-5.7 5.2 1.6 7.6L12 17.8 5.1 21.7l1.6-7.6L1 8.9 8.7 8z" fill="#1b1b1b"/></svg>
  <svg width="24" height="24" viewBox="0 0 24 24"><path d="M12 1l3.3 7 7.7.9-5.7 5.2 1.6 7.6L12 17.8 5.1 21.7l1.6-7.6L1 8.9 8.7 8z" fill="#1b1b1b"/></svg>
  <svg width="24" height="24" viewBox="0 0 24 24"><path d="M12 1l3.3 7 7.7.9-5.7 5.2 1.6 7.6L12 17.8 5.1 21.7l1.6-7.6L1 8.9 8.7 8z" fill="#1b1b1b"/></svg>
  <svg width="24" height="24" viewBox="0 0 24 24"><path d="M12 1l3.3 7 7.7.9-5.7 5.2 1.6 7.6L12 17.8 5.1 21.7l1.6-7.6L1 8.9 8.7 8z" fill="#1b1b1b"/></svg>
</div>
<div class="abs author">- Maren</div>

<!-- brand band -->
<section class="abs cta" role="img" aria-label="Blue-tinted gym background">
  <h2 class="abs display">Corvane Athletics</h2>
  <p class="abs">Lorem ipsum dolor sit amet, consectetur adipiscing elit, sed do eiusmod tempor incididunt ut labore et dolore magna aliqua. Quis ipsum suspendisse ultrices gravida. Risus commodo viverra maecenas accumsan lacus vel facilisis.</p>
  <div class="btn btn-blue" style="left:424px;top:313px;width:142px;height:45px">Join the Gym
    <svg width="12" height="12" viewBox="0 0 12 12"><path d="M1 1l10 10M11 4v7H4" fill="none" stroke="#fff" stroke-width="1.5"/></svg></div>
  <div class="btn btn-orange" style="left:585px;top:313px;width:190px;height:45px">Buy an Online Program</div>
</section>

<!-- blog -->
<h2 class="abs display blog-title">OUR BLOG</h2>
<article class="post" style="left:138px">
  <div class="img" role="img" aria-label="Athlete curling a barbell in a dark gym" style="background:linear-gradient(135deg,#0d0f12,#3e4449 50%,#15181b)"></div>
  <h4>Lorem ipsum dolor sit amet, consectetur adipiscing elit, sed do eiusmod tempor</h4>
  <div class="meta"><svg width="11" height="12" viewBox="0 0 11 12"><circle cx="5.5" cy="3.5" r="2.6" fill="none" stroke="#555" stroke-width="1.1"/><path d="M1 11.5c0-2.5 2-4 4.5-4s4.5 1.5 4.5 4" fill="none" stroke="#555" stroke-width="1.1"/></svg>by &nbsp;Dale Morrow &nbsp; Jul 13, 23</div>
</article>
<article class="post" style="left:453px">
  <div class="img" role="img" aria-label="Athlete setting up a deadlift" style="background:linear-gradient(135deg,#1f1c19,#5a5148 50%,#1a1816)"></div>
  <h4>Lorem ipsum dolor sit amet, consectetur adipiscing elit, sed do eiusmod tempor</h4>
  <div class="meta"><svg width="11" height="12" viewBox="0 0 11 12"><circle cx="5.5" cy="3.5" r="2.6" fill="none" stroke="#555" stroke-width="1.1"/><path d="M1 11.5c0-2.5 2-4 4.5-4s4.5 1.5 4.5 4" fill="none" stroke="#555" stroke-width="1.1"/></svg>by &nbsp;Dale Morrow &nbsp; Jul 13, 23</div>
</article>
<article class="post" style="left:768px">
  <div class="img" role="img" aria-label="Trainer standing with arms crossed in a gym" style="background:linear-gradient(135deg,#202327,#54585d 50%,#1c1e21)"></div>
  <h4>Lorem ipsum dolor sit amet, consectetur adipiscing elit, sed do eiusmod tempor</h4>
  <div class="meta"><svg width="11" height="12" viewBox="0 0 11 12"><circle cx="5.5" cy="3.5" r="2.6" fill="none" stroke="#555" stroke-width="1.1"/><path d="M1 11.5c0-2.5 2-4 4.5-4s4.5 1.5 4.5 4" fill="none" stroke="#555" stroke-width="1.1"/></svg>by &nbsp;Dale Morrow &nbsp; Jul 13, 23</div>
</article>

<!-- newsletter -->
<section class="abs news">
  <h2 class="abs">NEWSLETTER</h2>
  <div class="abs field">Email
    <div class="send"><svg width="18" height="14" viewBox="0 0 18 14"><rect x="1" y="1" width="16" height="12" rx="1.5" fill="none" stroke="#fff" stroke-width="1.5"/><path d="M1.5 2 9 8l7.5-6" fill="none" stroke="#fff" stroke-width="1.5"/></svg></div>
  </div>
</section>

<!-- footer -->
<footer class="abs footer">
  <div class="fcol" style="left:139px"><h5>Your Account</h5><ul><li>Personal Info</li><li>Orders</li><li>My Cart</li><li>Addresses</li></ul></div>
  <div class="fcol" style="left:371px"><h5>Customer Service</h5><ul>
    <li><svg width="13" height="13" viewBox="0 0 13 13"><circle cx="6.5" cy="6.5" r="6" fill="#fff"/><path d="M6.5 3v4h3" fill="none" stroke="#0c0d0f" stroke-width="1.3"/></svg>Monday to Friday</li>
    <li style="padding-left:25px">10am - 6.30pm</li>
    <li><svg width="13" height="13" viewBox="0 0 13 13"><path d="M3 1l2 3-1.3 1.3a7 7 0 003.9 3.9L9 8l3 2-1 2C5 12 1 8 1 2z" fill="#fff"/></svg>555 0142 876</li>
    <li><svg width="13" height="10" viewBox="0 0 13 10"><rect width="13" height="10" rx="1" fill="#fff"/><path d="M1 1l5.5 4.5L12 1" fill="none" stroke="#0c0d0f" stroke-width="1.2"/></svg>info@corvaneathletics.example</li>
  </ul></div>
  <div class="fcol" style="left:612px"><h5>Our Guarantees</h5><ul><li>Shipping in 3 days</li><li>Free returns within 14 days</li><li>Secure payments</li></ul></div>
  <div class="fcol" style="left:846px"><h5>Our Company</h5><ul><li>Home</li><li>About us</li><li>Programs</li><li>Shop</li><li>Contact us</li><li>Terms and conditions of use</li></ul></div>
  <svg class="abs" style="left:1126px;top:254px" width="12" height="14" viewBox="0 0 12 14"><path d="M6 13V2M1.5 6.5 6 2l4.5 4.5" fill="none" stroke="#fff" stroke-width="1.5"/></svg>
  <div class="abs frule"></div>
  <div class="abs legal"><span>© 2025, www.corvaneathletics.example</span><span>Refund policy</span><span>Privacy policy</span><span>Terms of service</span></div>
  <div class="abs pay"><i></i><i></i><i></i><i></i></div>
  <div class="abs social"><i></i><i></i><i></i><i></i><i></i></div>
</footer>

</body>
</html>
```